Business card for Luxury Portable Restroom Trailer company

We are a Luxury Portable Restroom Trailer Company Called FALCRIDGE HIRES. Based in Orange County California. We provide portable restroom trailers for events, such as, Weddings, Concerts, Charity events, Sporting events, Tournaments, Corporate events, ect. We rent and Sell the Luxury restrooms. Our colors are white, grey, and Orange. As you will see in the logo we uploaded.
There are 2 people in the company so the names and titles will change for the 3 people but card will remain the same. Here is the information for each Person: Dwight Penner CFO 555 318-0476
next Person: Leon Marchetti VP 555 318-0476
Next Person: Owen Marchetti CEO 555 318-0476
Information to include on the card: Luxury Restroom Trailers Rental and Sales. Weddings, Concerts, Charity, Sporting and Corp. Events.

```html
<!DOCTYPE html>
<html lang="en">
<head>
<meta charset="utf-8">
<title>Falcridge Hires — Business Card</title>
<link href="https://fonts.googleapis.com/css2?family=Roboto:wght@400;700&display=swap" rel="stylesheet">
<style>
  :root{
    --page:#1e1e1e;
    --card-dark:#2b2b2b;
    --emboss:#3a3a3a;
    --card-light:#e6e6e6;
    --stripe:#6b6b6b;
    --orange:#d4703e;
    --edge:#f06a1e;
    --white:#ffffff;
    --grey-text:#5f5f5f;
  }
  *{box-sizing:border-box;margin:0;padding:0}
  html,body{width:1200px;height:874px;overflow:hidden}
  body{
    background:var(--page);
    font-family:"Roboto",Arial,sans-serif;
    display:flex;flex-direction:column;align-items:center;justify-content:center;gap:40px;
  }
  .card{
    width:630px;height:360px;border-radius:22px;overflow:hidden;position:relative;
    border:2px solid var(--edge);
  }

  /* back side */
  .card--back{background:var(--card-dark);display:flex;flex-direction:column;align-items:center}
  .card--back .wordmark{
    margin-top:112px;color:var(--emboss);font-weight:700;font-size:50px;letter-spacing:2px;
    display:flex;align-items:center;gap:14px;
  }
  .wordmark__dot{width:26px;height:26px;background:currentColor;display:inline-block}
  .tagline{
    margin-top:auto;margin-bottom:36px;color:var(--white);text-align:center;
    font-size:16px;line-height:1.45;
  }

  /* front side */
  .card--front{background:var(--card-light)}
  .card--front .wordmark{
    position:absolute;top:70px;left:0;right:0;justify-content:center;
    color:var(--orange);font-weight:700;font-size:46px;letter-spacing:2px;
    display:flex;align-items:center;gap:14px;
  }
  .stripe{position:absolute;left:0;right:0;top:168px;height:9px;background:var(--stripe)}
  .contact-band{
    position:absolute;left:0;right:0;top:177px;bottom:0;background:var(--orange);
    display:flex;align-items:center;padding:0 0 0 70px;color:var(--white);
  }
  .person{text-align:right;padding-right:20px;border-right:2px solid var(--white);padding-top:4px;padding-bottom:10px}
  .person__name{font-weight:700;font-size:25px;text-transform:uppercase}
  .person__title{font-size:17px;margin-top:4px}
  .contact-list{list-style:none;padding-left:20px;font-size:18px;line-height:1.55}
  .contact-list li{display:flex;align-items:center;gap:10px}
  .contact-list svg{width:15px;height:15px;fill:var(--white);flex:none}
</style>
</head>
<body>

  <section class="card card--back">
    <div class="wordmark"><span class="wordmark__dot"></span>FALCRIDGE HIRES</div>
    <p class="tagline">
      Luxury Restroom Trailers Rental and Sales.<br>
      Weddings • Concerts • Charity • Sporting and Corp. Events
    </p>
  </section>

  <section class="card card--front">
    <div class="wordmark"><span class="wordmark__dot"></span>FALCRIDGE HIRES</div>
    <div class="stripe"></div>
    <div class="contact-band">
      <div class="person">
        <div class="person__name">Dwight Penner</div>
        <div class="person__title">CFO</div>
      </div>
      <ul class="contact-list">
        <li>
          <svg viewBox="0 0 24 24" aria-hidden="true"><path d="M6.6 10.8a15.1 15.1 0 0 0 6.6 6.6l2.2-2.2a1 1 0 0 1 1-.25 11.4 11.4 0 0 0 3.6.57 1 1 0 0 1 1 1V20a1 1 0 0 1-1 1A17 17 0 0 1 3 4a1 1 0 0 1 1-1h3.5a1 1 0 0 1 1 1c0 1.25.2 2.45.57 3.57a1 1 0 0 1-.25 1z"/></svg>
          555 318-0476
        </li>
        <li>
          <svg viewBox="0 0 24 24" aria-hidden="true"><path d="M2 5h20v14H2z M2 5l10 8 10-8" fill="none" stroke="#fff" stroke-width="2"/></svg>
          info@falcridgehires.com
        </li>
        <li>
          <svg viewBox="0 0 24 24" aria-hidden="true"><circle cx="12" cy="12" r="9" fill="none" stroke="#fff" stroke-width="2"/><path d="M3 12h18M12 3c3 3 3 15 0 18M12 3c-3 3-3 15 0 18" fill="none" stroke="#fff" stroke-width="1.6"/></svg>
          www.falcridgehires.com
        </li>
      </ul>
    </div>
  </section>

</body>
</html>
```